RESIDENTIAL CONSTRUCTION

We are a company that specializes in building custom residential homes, the design should also emphasize that quality and service is our priority.

Industry/Entity Type

Construction Company

Contact Information for Business Card

Contact Person: Marcus Lindqvist
Company Address: 273 West Alder Ave San Jose , Ca 95380
Phone Number : 408-731-2946
Email Address: Stoneridgehomes517@mailvista.net

Font styles to use
Sans Serif

Colors
ec1f27

Requirements
Must have
• CSLB # 7362015
Nice to have
• needs to have same color as logo i uploaded, we will be printing these on a clear plastic card.

```html
<!DOCTYPE html>
<html lang="en">
<head>
<meta charset="utf-8">
<title>Stoneridge Homes – Business Card</title>
<link href="https://fonts.googleapis.com/css2?family=Oswald:wght@600&family=Roboto:wght@400;700&display=swap" rel="stylesheet">
<style>
  :root {
    --brand-red: #ec1f27;
    --deep-red: #c41a22;
    --ink: #1a1a1a;
    --text-grey: #8a8a8a;
    --paper: #ffffff;
    --backdrop: #e9e7e3;
    --mark-tint: rgba(236, 31, 39, 0.10);
  }
  * { box-sizing: border-box; margin: 0; padding: 0; }
  html, body {
    width: 1200px;
    height: 950px;
    overflow: hidden;
    background: var(--backdrop);
    font-family: "Roboto", Arial, sans-serif;
  }
  .stage {
    width: 1200px;
    height: 950px;
    display: flex;
    align-items: center;
    justify-content: center;
  }
  .business-card {
    position: relative;
    width: 1050px;
    height: 600px;
    background: var(--paper);
    box-shadow: 0 12px 40px rgba(0, 0, 0, 0.18);
    overflow: hidden;
  }
  .brand-lockup {
    position: absolute;
    top: 70px;
    right: 70px;
    display: flex;
    align-items: center;
    gap: 18px;
  }
  .brand-square {
    width: 62px;
    height: 62px;
    background: var(--brand-red);
  }
  .brand-name {
    font-family: "Oswald", "Arial Narrow", sans-serif;
    font-weight: 600;
    font-size: 60px;
    line-height: 1;
    letter-spacing: 1px;
    text-transform: uppercase;
    color: var(--brand-red);
  }
  .background-mark {
    position: absolute;
    left: 40px;
    top: 170px;
    width: 420px;
    height: 300px;
    background: radial-gradient(ellipse at 40% 50%, var(--mark-tint), rgba(236, 31, 39, 0) 70%);
  }
  .name-tab {
    position: absolute;
    left: 0;
    top: 276px;
    width: 42px;
    height: 18px;
    background: var(--brand-red);
  }
  .contact-block {
    position: absolute;
    left: 70px;
    top: 258px;
  }
  .person-name {
    font-weight: 700;
    font-size: 40px;
    letter-spacing: 0.5px;
    text-transform: uppercase;
    color: var(--brand-red);
    margin-bottom: 30px;
  }
  .contact-lines {
    list-style: none;
    margin-left: 200px;
    font-size: 24px;
    line-height: 34px;
    color: var(--text-grey);
  }
  .contact-lines li {
    display: flex;
    align-items: center;
    gap: 12px;
  }
  .contact-icon {
    width: 22px;
    height: 22px;
    flex: none;
  }
  .bottom-band {
    position: absolute;
    left: 0;
    right: 0;
    bottom: 0;
    height: 30px;
    background: var(--brand-red);
    border-top: 4px solid var(--deep-red);
  }
</style>
</head>
<body>
<main class="stage">
  <article class="business-card">
    <div class="brand-lockup">
      <span class="brand-square"></span>
      <span class="brand-name">Stoneridge Homes</span>
    </div>

    <div class="background-mark" role="img" aria-label="Faint house and drafting compass illustration"></div>

    <span class="name-tab"></span>

    <section class="contact-block">
      <h1 class="person-name">Marcus Lindqvist</h1>
      <ul class="contact-lines">
        <li>273 West Alder Ave San Jose</li>
        <li>Ca 95380</li>
        <li>CSLB # 7362015</li>
        <li>
          <svg class="contact-icon" viewBox="0 0 24 24" aria-hidden="true">
            <path fill="#ec1f27" d="M6.6 10.8a15 15 0 0 0 6.6 6.6l2.2-2.2a1 1 0 0 1 1-.25 11.4 11.4 0 0 0 3.6.57 1 1 0 0 1 1 1V20a1 1 0 0 1-1 1A17 17 0 0 1 3 4a1 1 0 0 1 1-1h3.5a1 1 0 0 1 1 1c0 1.25.2 2.45.57 3.57a1 1 0 0 1-.25 1z"/>
          </svg>
          408-731-2946
        </li>
        <li>
          <svg class="contact-icon" viewBox="0 0 24 24" aria-hidden="true">
            <rect x="2" y="5" width="20" height="14" rx="1" fill="#ec1f27"/>
            <path d="M3 6l9 7 9-7" fill="none" stroke="#ffffff" stroke-width="1.6"/>
          </svg>
          Stoneridgehomes517@mailvista.net
        </li>
        <li>
          <svg class="contact-icon" viewBox="0 0 24 24" aria-hidden="true">
            <circle cx="12" cy="12" r="10" fill="#ec1f27"/>
            <path d="M2 12h20M12 2c3 3 3 17 0 20M12 2c-3 3-3 17 0 20" fill="none" stroke="#ffffff" stroke-width="1.3"/>
          </svg>
          www.stoneridgehomes-ca.com
        </li>
      </ul>
    </section>

    <div class="bottom-band"></div>
  </article>
</main>
</body>
</html>
```